NEW Wordpress Website Design for a Dynamic Long Term Healthcare Company in Hawaii

I would like a new website design for my current company, Marlow Health Collective, which has two different brands - Marlow Homecare and Marlow Senior Living. You can see the current website at www.marlowhealth-example.com. The website should be built using Wordpress Software and the Framewise theme. The website should have a local Hawaii island/tropical feel, but look professional for healthcare. I'm looking for something fresh, and want the designer to select colors, styles, etc.

In the Header, on all pages, I would like a menu that includes Home Care, Senior Living, Rates, and About Us.
Under each of the Header Menu Titles, I would like these drop downs included:
Home Care (drop down pages)- Nurse Aide Care, 24-Hour Home Care, Skilled Nursing, Lifestyle Aide, Hospice at Home, Bathing & Meal Service.
Senior Living (drop down pages) - Long-Term Stay, Short-Term Stay.
Rates (drop down page) - Rates.
About Us (drop down pages) - Our Mission, Ohana Talk, About Dana Marlow.

In the footer, on all pages, you should include the address: 248 Pueo Lane, Suite 310, Honolulu, HI 96817. Phone number: 808-555-0172
The footer should also include buttons for a page called Learn, Caregiver Jobs, and each of the service page links to include: Nurse Aide Care, 24-Hour Home Care, Skilled Nursing, Lifestyle Aide, Hospice at Home, Bathing & Meal Service.
Please don't take the current website and redesign a few aspects. I'm looking for a completely different look and feel.

Target Market(s)

40-80 year olds

Industry/Entity Type

Long Term Healthcare

Coding

Coded - Design and coding required

Requirements
Should not have
• Our existing website as a template. We are looking for a complete redesign. Thank you.

```html
<!DOCTYPE html>
<html lang="en">
<head>
<meta charset="utf-8">
<title>Marlow Health Collective — Homecare &amp; Senior Living</title>
<link rel="stylesheet" href="https://fonts.googleapis.com/css2?family=Playfair+Display:wght@400;500;700&family=Montserrat:wght@400;500;600&display=swap">
<style>
:root{
  --coral:#f47c72;
  --coral-soft:#fde3e0;
  --blue:#3aaee8;
  --blue-soft:#dcefff;
  --green:#7cb342;
  --ink:#1f1f1f;
  --text:#2b2b2b;
  --muted:#777;
  --white:#fff;
  --field:#f4f4f4;
  --serif:'Playfair Display',Georgia,serif;
  --sans:'Montserrat',Arial,sans-serif;
}
*{box-sizing:border-box;margin:0;padding:0}
html,body{width:1200px;height:4804px;overflow:hidden}
body{font-family:var(--sans);color:var(--text);background:var(--white);position:relative}
.coral{color:var(--coral)}
.blue{color:var(--blue)}
.green{color:var(--green)}

/* header */
.site-header{position:absolute;top:0;left:0;width:1200px;height:148px;background:var(--white);border-bottom:5px solid var(--coral)}
.brand-row{position:absolute;left:75px;top:38px;display:flex;gap:26px;align-items:center}
.brand{display:flex;align-items:center;gap:8px;font-family:var(--serif);font-size:22px;color:var(--ink);white-space:nowrap}
.brand .dot{width:18px;height:18px;border-radius:50%;flex:none}
.call-btn{position:absolute;left:860px;top:22px;width:264px;height:46px;border:2px solid #333;border-radius:8px;display:flex;align-items:center;justify-content:center;font-size:22px;letter-spacing:.5px}
.main-nav{position:absolute;top:100px;left:545px;display:flex;gap:26px;font-size:20px}
.main-nav span{display:flex;align-items:center;gap:10px}
.main-nav svg{width:16px;height:12px}

/* hero */
.hero{position:absolute;top:153px;left:0;width:1200px;height:537px;background:linear-gradient(120deg,#7a5a2a 0%,#c8b95a 30%,#d9cf63 55%,#9c8e3c 80%,#6a4a24 100%)}
.hero-panel{position:absolute;left:150px;top:52px;width:900px;height:355px;background:rgba(255,255,255,.55);text-align:center;padding-top:52px}
.hero-panel .kicker{font-size:16px}
.hero-panel h1{font-family:var(--serif);font-size:50px;font-weight:500;letter-spacing:1px;line-height:1.2;color:var(--ink)}
.hero-panel .title2{font-family:var(--serif);font-size:52px;line-height:1.3;margin-top:2px}
.hero-panel p{font-size:18.5px;line-height:1.3;margin:20px auto 0;width:700px}
.tab-card{position:absolute;z-index:5;left:62px;top:618px;width:1074px;height:139px;background:var(--white);border-bottom:6px solid var(--coral);box-shadow:0 8px 22px rgba(0,0,0,.08);border-radius:4px;font-family:var(--serif);font-size:30px}
.tab-card span{position:absolute;top:48px}

/* services */
.services{position:absolute;top:690px;left:0;width:1200px;height:960px;background:linear-gradient(180deg,#fff 10%,#fde7e4 60%,#fbd3cf 100%)}
.section-title{font-family:var(--serif);font-size:31px;font-weight:500;text-align:center;color:var(--ink)}
.section-lead{font-size:18.5px;line-height:1.3;text-align:center;width:880px;margin:10px auto 0}
.card{position:absolute;width:258px;background:var(--white);text-align:center;padding:14px 16px 0;box-shadow:0 4px 14px rgba(0,0,0,.05)}
.card.c-coral{border-bottom:5px solid var(--coral)}
.card.c-blue{border-bottom:5px solid var(--blue);width:374px}
.card svg{width:56px;height:48px}
.card h3{font-family:var(--serif);font-weight:500;font-size:18px;margin:10px 0 14px}
.card p{font-size:18px;line-height:1.3}
.btn{position:absolute;display:flex;align-items:center;justify-content:center;color:var(--white);font-family:var(--serif);font-size:18px;letter-spacing:.5px;border-radius:6px;box-shadow:0 4px 10px rgba(0,0,0,.12)}
.btn.coral-bg{background:var(--coral)}
.btn.blue-bg{background:var(--blue)}

/* photo strips */
.strip{position:absolute;left:0;width:1200px;height:366px;display:flex}
.strip .ph{height:100%}

/* senior living */
.senior{position:absolute;top:2016px;left:0;width:1200px;height:627px;background:linear-gradient(180deg,#fff 5%,#e4f2fd 55%,#cfe8fb 100%)}

/* mission band */
.mission{position:absolute;top:3008px;left:0;width:1200px;height:740px;background:linear-gradient(90deg,#ffffff 0%,#cfeaf0 30%,#7fc7d9 55%,#e8ddd3 80%,#f6efe9 100%)}
.mission-box{position:absolute;left:52px;top:325px;width:688px;height:368px;background:rgba(200,200,200,.6);padding:82px 50px 0}
.mission-box h2{font-family:var(--serif);font-weight:500;font-size:31px;color:var(--ink)}
.mission-box p{font-size:18.5px;line-height:1.3;margin-top:34px;width:560px}

/* consultation */
.consult-title{position:absolute;left:55px;top:3866px;font-family:var(--serif);font-size:31px;font-weight:500;line-height:1.4;color:var(--ink)}
.form{position:absolute;left:55px;top:3988px;width:393px}
.field{height:32px;background:var(--field);font-size:11px;color:var(--muted);display:flex;align-items:center;justify-content:space-between;padding:0 10px;margin-bottom:11px}
.field.tall{height:68px}
.field svg{width:10px;height:7px}
.consent{font-size:9px;color:#555;margin:6px 0 10px;text-align:center}
.submit{height:42px;border-radius:6px;background:var(--blue);color:var(--white);font-family:var(--serif);font-size:20px;display:flex;align-items:center;justify-content:center}
.consult-photo{position:absolute;left:530px;top:3800px;width:670px;height:670px;background:linear-gradient(135deg,#f3efe9 0%,#e6d8c7 45%,#c9a98b 75%,#f1e9df 100%)}

/* footer */
.site-footer{position:absolute;top:4472px;left:0;width:1200px;height:332px;border-top:5px solid var(--coral);background:var(--white)}
.foot-brands{position:absolute;left:60px;top:95px;display:flex;gap:14px;align-items:center}
.foot-brands .brand{font-size:15px;gap:6px}
.foot-brands .dot{width:13px;height:13px}
.copy{position:absolute;left:108px;top:228px;font-size:11px;color:#444}
.foot-h{position:absolute;font-size:11px;font-weight:600;letter-spacing:1px}
.foot-col{position:absolute;font-size:11px;line-height:34px;color:#333}
.foot-contact{position:absolute;left:850px;width:280px;text-align:center;font-size:11px;color:#333}
.social{position:absolute;left:950px;top:180px;display:flex;gap:10px}
.social span{width:12px;height:12px;border-radius:50%;background:#333}
</style>
</head>
<body>

<header class="site-header">
  <div class="brand-row">
    <div class="brand"><span class="dot" style="background:var(--coral)"></span>Marlow Homecare</div>
    <div class="brand"><span class="dot" style="background:var(--ink)"></span>Marlow</div>
    <div class="brand"><span class="dot" style="background:#6fb3a6"></span>Senior Living</div>
  </div>
  <div class="call-btn">CALL (808) 555-0172</div>
  <nav class="main-nav">
    <span>Home Care <svg viewBox="0 0 16 12"><path d="M0 0h16L8 12z" fill="#f47c72"/></svg></span>
    <span>Senior Living <svg viewBox="0 0 16 12"><path d="M0 0h16L8 12z" fill="#f47c72"/></svg></span>
    <span>Rates <svg viewBox="0 0 16 12"><path d="M0 0h16L8 12z" fill="#f47c72"/></svg></span>
    <span>About Us <svg viewBox="0 0 16 12"><path d="M0 0h16L8 12z" fill="#f47c72"/></svg></span>
  </nav>
</header>

<section class="hero" role="img" aria-label="Photo of caregivers and seniors sharing a craft activity in a warm, sunlit living room">
  <div class="hero-panel">
    <div class="kicker">WELCOME TO</div>
    <h1>HAWAII'S CHOICE</h1>
    <div class="title2"><span class="coral">HOMECARE</span> <span style="color:var(--ink)">&amp;</span> <span class="blue">SENIOR LIVING</span></div>
    <p>Marlow Homecare provides a variety of professional in-home health care services throughout the entire island of Oahu.<br>Marlow Senior Living, a beautiful Adult Residential Care Home, is located on the windward side of Oahu in Kailua.</p>
  </div>
</section>

<section class="services">
  <h2 class="section-title" style="margin-top:168px">Comprehensive <span class="coral">Home Care</span> Services with Heart</h2>
  <p class="section-lead">From skilled nursing to lifestyle aid, our expert caregivers bring compassionate care into your home, helping you or your loved ones live independently</p>

  <div class="card c-coral" style="left:165px;top:310px;height:208px">
    <svg viewBox="0 0 56 48"><path d="M8 14 Q28 2 48 14 L42 38 H14 Z" fill="none" stroke="#f47c72" stroke-width="2.5"/><path d="M28 18v12M22 24h12" stroke="#f47c72" stroke-width="2.5"/></svg>
    <h3 class="coral">Nurse Aide Care</h3>
    <p>Professional support to assist with daily needs and personal care.</p>
  </div>
  <div class="card c-coral" style="left:470px;top:310px;height:208px">
    <svg viewBox="0 0 56 48"><circle cx="28" cy="24" r="17" fill="none" stroke="#f47c72" stroke-width="2.5" stroke-dasharray="80 10"/><text x="28" y="29" font-size="13" font-weight="600" text-anchor="middle" fill="#f47c72" font-family="Montserrat,sans-serif">24</text></svg>
    <h3 class="coral">24-Hour Home Care</h3>
    <p>Round-the-clock assistance tailored to meet all your needs.</p>
  </div>
  <div class="card c-coral" style="left:775px;top:310px;height:208px">
    <svg viewBox="0 0 56 48"><circle cx="28" cy="14" r="8" fill="none" stroke="#f47c72" stroke-width="2.5"/><path d="M12 42 Q12 26 28 26 Q44 26 44 42 Z" fill="none" stroke="#f47c72" stroke-width="2.5"/><path d="M28 10v8M24 14h8" stroke="#f47c72" stroke-width="2"/></svg>
    <h3 class="coral">Skilled Nursing</h3>
    <p>Experienced nurses providing medical care at home.</p>
  </div>
  <div class="card c-coral" style="left:165px;top:555px;height:230px">
    <svg viewBox="0 0 56 48"><circle cx="18" cy="12" r="6" fill="none" stroke="#f47c72" stroke-width="2.5"/><circle cx="38" cy="12" r="6" fill="none" stroke="#f47c72" stroke-width="2.5"/><rect x="9" y="24" width="18" height="18" rx="6" fill="none" stroke="#f47c72" stroke-width="2.5"/><rect x="29" y="24" width="18" height="18" rx="6" fill="none" stroke="#f47c72" stroke-width="2.5"/></svg>
    <h3 class="coral">Lifestyle Aide</h3>
    <p>Helping with errands, companionship, and maintaining your lifestyle.</p>
  </div>
  <div class="card c-coral" style="left:470px;top:566px;height:208px">
    <svg viewBox="0 0 56 48"><path d="M28 6 L48 24 V42 H8 V24 Z" fill="#f47c72"/><path d="M28 22v12M22 28h12" stroke="#fff" stroke-width="3"/></svg>
    <h3 class="coral">Hospice at Home</h3>
    <p>Comforting care to ensure peace in difficult times.</p>
  </div>
  <div class="card c-coral" style="left:775px;top:555px;height:230px">
    <svg viewBox="0 0 56 48"><path d="M28 4v14M21 11h14" stroke="#f47c72" stroke-width="4"/><path d="M6 36 H20 Q26 30 34 32 H46 Q50 34 46 38 L34 44 H6 Z" fill="#f47c72"/></svg>
    <h3 class="coral">Bathing &amp; Meal Service</h3>
    <p>Daily hygiene and meal preparation support, ensuring dignity and care</p>
  </div>
  <div class="btn coral-bg" style="left:424px;top:825px;width:352px;height:60px">SCHEDULE CARE ASSESSMENT</div>
</section>

<nav class="tab-card" aria-label="Choose a service">
  <span class="coral" style="left:234px">HOMECARE</span>
  <span class="blue" style="left:611px">SENIOR LIVING</span>
</nav>

<div class="strip" style="top:1650px">
  <div class="ph" style="width:376px;background:linear-gradient(135deg,#b89a5e,#e5dcb4 50%,#8a6a3a)" role="img" aria-label="Photo of a caregiver serving a meal to seniors at a dining table"></div>
  <div class="ph" style="width:436px;background:linear-gradient(135deg,#d6cf8a,#efe6b8 50%,#a8874e)" role="img" aria-label="Photo of a caregiver assisting a senior man seated on a bed"></div>
  <div class="ph" style="width:388px;background:linear-gradient(135deg,#e4ddb0,#c7b98a 50%,#6b8fa8)" role="img" aria-label="Photo of caregivers and a resident relaxing on a sofa"></div>
</div>

<section class="senior">
  <h2 class="section-title" style="margin-top:78px">Aloha in Every Moment of <span class="blue">Senior Living</span></h2>
  <p class="section-lead" style="width:900px">Our senior living options offer comfort, community, and care in a tropical paradise. Whether for short-term or long-term stays, we ensure a home-like experience.</p>
  <div class="card c-blue" style="left:202px;top:222px;height:230px">
    <svg viewBox="0 0 56 48"><path d="M8 14 Q28 2 48 14 L42 38 H14 Z" fill="none" stroke="#3aaee8" stroke-width="2.5"/><path d="M28 18v12M22 24h12" stroke="#3aaee8" stroke-width="2.5"/></svg>
    <h3 class="blue">Long-Term Stay</h3>
    <p>A welcoming community for those who need ongoing support</p>
  </div>
  <div class="card c-blue" style="left:622px;top:222px;height:230px">
    <svg viewBox="0 0 56 48"><circle cx="28" cy="24" r="17" fill="none" stroke="#3aaee8" stroke-width="2.5" stroke-dasharray="80 10"/><text x="28" y="29" font-size="13" font-weight="600" text-anchor="middle" fill="#3aaee8" font-family="Montserrat,sans-serif">24</text></svg>
    <h3 class="blue">Short-Term Stay</h3>
    <p>Round-the-clock assistance tailored to meet all your needs.</p>
  </div>
  <div class="btn blue-bg" style="left:490px;top:494px;width:220px;height:58px">SCHEDULE TOUR</div>
</section>

<div class="strip" style="top:2643px">
  <div class="ph" style="width:376px;background:linear-gradient(135deg,#3f6b2f,#9cc46a 50%,#c9c9b6)" role="img" aria-label="Photo of a caregiver walking with a senior using a walker in a garden"></div>
  <div class="ph" style="width:436px;background:linear-gradient(135deg,#d8cf88,#b88d5a 50%,#e8e2c0)" role="img" aria-label="Photo of seniors doing a light exercise class with dumbbells"></div>
  <div class="ph" style="width:388px;background:linear-gradient(135deg,#e4ddb0,#c7b98a 50%,#6b8fa8)" role="img" aria-label="Photo of caregivers and a resident relaxing on a sofa"></div>
</div>

<section class="mission" role="img" aria-label="Photo of a smiling nurse leaning close to a senior man">
  <div class="mission-box">
    <h2>Dedicated to Serving Hawaii’s Ohana</h2>
    <p>Founded by Dana Marlow, our mission is to provide compassionate, high-quality care to families across Hawaii.</p>
  </div>
  <div class="btn blue-bg" style="left:100px;top:557px;width:220px;height:58px">SCHEDULE TOUR</div>
</section>

<h2 class="consult-title">Schedule a <span class="green">complimentary</span><br>Care Consultation</h2>
<form class="form">
  <div class="field">Name*</div>
  <div class="field">Email*</div>
  <div class="field">Phone*</div>
  <div class="field">How Can We Help?<svg viewBox="0 0 10 7"><path d="M0 0h10L5 7z" fill="#f47c72"/></svg></div>
  <div class="field tall">Questions/comments</div>
  <div class="field">Where did you hear about is?</div>
  <div class="field">May We Email You About This?<svg viewBox="0 0 10 7"><path d="M0 0h10L5 7z" fill="#f47c72"/></svg></div>
  <p class="consent">You agree to receive future emails and understand you may opt-out at any time</p>
  <div class="submit">Submit</div>
</form>
<div class="consult-photo" role="img" aria-label="Photo of a caregiver and a senior woman smiling while looking at a photo album"></div>

<footer class="site-footer">
  <div class="foot-brands">
    <div class="brand"><span class="dot" style="background:var(--coral)"></span>Marlow Homecare</div>
    <div class="brand"><span class="dot" style="background:var(--ink)"></span>Marlow</div>
    <div class="brand"><span class="dot" style="background:#6fb3a6"></span>Senior Living</div>
  </div>
  <p class="copy">© 2023 Marlow Health Collective. All Rights Reserved</p>

  <div class="foot-h" style="left:604px;top:46px">LINKS</div>
  <div class="foot-col" style="left:495px;top:78px">Home<br>Contact<br>Learn<br>Caregiver Jobs<br>Privacy Policy</div>
  <div class="foot-col" style="left:612px;top:78px">Nurse Aide Care<br>24-Hour Home Care<br>Skilled Nursing<br>Lifestyle Aide<br>Hospice at Home<br>Bathing &amp; Meal Service</div>

  <div class="foot-h" style="left:962px;top:46px">CONTACT</div>
  <div class="foot-contact" style="top:90px">808-555-0172</div>
  <div class="foot-contact" style="top:122px">248 Pueo Lane, Suite 310, Honolulu, HI 96817</div>
  <div class="social"><span></span><span></span><span></span></div>
</footer>

</body>
</html>
```